Bright Harbor Learning Center Brochure Design

We are looking for a visually appealing and well-structured tri-fold brochure that effectively communicates our mission, values, and offerings. The brochure should be engaging, informative, and eye-catching, ensuring that families can easily connect with our message.
Key Requirements:
- Front Cover: Must include our Bright Harbor Learning Center logo and a compelling design that draws attention.
- Back Panel: Should display our locations, social media handles, QR code, website, and phone number, arranged neatly for easy access. (Reference the attached example for layout inspiration.)
- Content & Imagery: The provided text must be incorporated in a clean, organized layout that flows naturally. We’ve also included photos of children we would like used. (Not all photos have to be used, just some)
- Design & Color Scheme: We are open to creative variations, but the overall aesthetic should feel cohesive, professional, and visually engaging. The design should capture the warmth, care, and discovery-based learning environment we provide.
- Attention-Grabbing & Readable: The brochure should be easy to read, with well-balanced text and imagery that doesn’t overwhelm the viewer.
We are excited to see your creative approach—make it stand out while maintaining clarity and professionalism!
---------------------------------------------------------------------------
This is the info that needs to be used:
Welcome to Bright Harbor Learning Center
Where Learning & Care Come Together!
At Bright Harbor, we go beyond childcare—we create a warm, nurturing community where families feel supported and confident in their child’s growth.
✅ Privately owned early learning centers with hands-on leadership
✅ Safe, engaging environments designed to inspire young minds
✅ Now transitioning to a Reggio Emilia-inspired approach—encouraging exploration, creativity, and child-led learning
We are also proud to offer exclusive corporate discounts for professionals in key industries:
🔹 Teachers
🔹 Healthcare & Hospital Staff
🔹 Law Enforcement & First Responders
🔹 Military Families
🔹 Employees of Partnered Businesses & Apartments
Quality childcare should be affordable and accessible—because when families thrive, communities grow!
Our Approach: Learning Through Exploration
At Bright Harbor, we believe that children learn best through curiosity, hands-on discovery, and meaningful experiences. That’s why we are transitioning to a Reggio Emilia-inspired philosophy, where:
✨ Children take the lead – Learning is shaped by their interests and natural curiosity
✨ Teachers are guides – Educators observe, support, and enrich children’s experiences
✨ The environment is a teacher – Classrooms are designed to inspire creativity and exploration
✨ Collaboration is key – Children, families, and educators work together in a connected learning community
We blend this philosophy with The Playwise Framework® for Preschool and Emergent Curriculum to create a research-backed, child-centered learning experience. The Playwise Framework® builds confidence, critical thinking, and academic readiness, while Emergent Curriculum adapts lessons to children's interests—making learning engaging, meaningful, and fun.
Our Mission: Growing Together
🌟 Building strong partnerships – Open communication with families & communities
🌟 Nurturing confidence & creativity – Every child is seen, heard, and supported
🌟 Fostering a lifelong love for learning – Through discovery, exploration & meaningful experiences
As we transition to a Reggio Emilia-inspired approach, we are excited to offer a learning experience that is more engaging, dynamic, and child-centered than ever before.
Imagine a place where every child’s voice is heard, creativity is celebrated, and learning is an adventure—welcome to Bright Harbor!

```html
<!DOCTYPE html>
<html lang="en">
<head>
<meta charset="utf-8">
<title>Bright Harbor Learning Center – Brochure Inside Spread</title>
<link rel="stylesheet" href="https://fonts.googleapis.com/css2?family=Luckiest+Guy&family=Lilita+One&family=Fredoka:wght@500;600&family=Quicksand:wght@500;600&display=swap">
<style>
  :root{
    --panel-light:#deebfb;
    --panel-teal:#2a96b8;
    --ink:#1d1d1f;
    --white:#ffffff;
    --pink:#ee3fa6;
    --green:#4cd964;
    --tick:#3ccb6a;
    --teal-head:#14c2b0;
    --dot-teal:#21c1b6;
    --dot-green:#4fd66e;
    --dot-pink:#ef3ea8;
  }
  *{box-sizing:border-box;margin:0;padding:0}
  html,body{width:1200px;height:849px;overflow:hidden;background:var(--panel-light)}
  .spread{position:relative;width:1200px;height:849px;font-family:"Quicksand",sans-serif;color:var(--ink)}
  .panel{position:absolute;top:0;height:849px;width:401px;overflow:hidden}
  .panel--left{left:0;background:var(--panel-light)}
  .panel--middle{left:401px;background:var(--panel-teal);color:var(--white)}
  .panel--right{left:802px;width:398px;background:var(--panel-light)}
  .abs{position:absolute}

  .title-sticker{position:absolute;background:var(--white);border-radius:22px;text-align:center;font-family:"Luckiest Guy","Lilita One",sans-serif;font-weight:400;line-height:1;padding:7px 8px 4px;text-transform:uppercase;white-space:nowrap}
  .title-main,.title-sub{display:block}

  .left-title{left:30px;top:45px;width:344px}
  .left-title .title-main{color:var(--pink);font-size:32px;letter-spacing:-0.5px}
  .left-title .title-sub{color:var(--green);font-size:21px;margin-top:2px}

  .body-copy{font-size:17px;line-height:19px;font-weight:500}
  .intro{left:32px;top:114px;width:345px;font-size:16.6px}

  .placeholder{position:absolute;border-radius:28px}
  .feature{position:absolute;font-size:16.5px;line-height:19px;font-weight:500}

  .photo{position:absolute;border-radius:50%;border:6px solid var(--white)}
  .dot{position:absolute;border-radius:50%}

  .discount-lead{left:20px;top:50px;width:375px;font-size:16.4px;line-height:19px}
  .discount-list{position:absolute;left:20px;top:107px;width:375px;list-style:none;font-family:"Fredoka",sans-serif;font-weight:600;font-size:16.5px;line-height:19px}
  .discount-list li{position:relative;padding-left:24px}
  .discount-list svg{position:absolute;left:0;top:2px}
  .discount-close{left:20px;top:226px;width:355px;font-size:16.4px;line-height:19px}

  .right-title{left:36px;top:44px;width:316px}
  .right-title .title-main{color:var(--teal-head);font-size:38px}
  .right-title .title-sub{color:var(--pink);font-size:14.5px;margin-top:1px}
  .approach-intro{left:21px;top:117px;width:358px}
  .principle{position:absolute;left:21px;width:358px}
  .principle h3{position:relative;font-family:"Fredoka",sans-serif;font-weight:600;font-size:17px;line-height:19px;padding-left:24px}
  .principle h3 svg{position:absolute;left:0;top:2px}
  .principle p{font-size:17px;line-height:19px;font-weight:500;hyphens:auto}
  .approach-blend{left:21px;top:532px;width:358px;hyphens:auto}
</style>
</head>
<body>
<main class="spread">

  <section class="panel panel--left">
    <h1 class="title-sticker left-title">
      <span class="title-main">At Bright Harbor</span>
      <span class="title-sub">We go beyond childcare</span>
    </h1>
    <p class="abs body-copy intro">we create a warm, nurturing community where families feel supported and confident in their child’s growth.</p>

    <div class="dot" style="left:42px;top:203px;width:10px;height:10px;background:var(--dot-teal)"></div>
    <div class="placeholder" role="img" aria-label="Illustration of a hand holding a shield with a check mark" style="left:29px;top:182px;width:143px;height:130px;background:linear-gradient(160deg,#d8d0f6,#f3c6c8)"></div>
    <p class="feature" style="left:195px;top:213px;width:200px">Privately owned early learning centers with hands-on leadership</p>

    <div class="dot" style="left:171px;top:301px;width:19px;height:19px;background:var(--dot-pink)"></div>
    <div class="dot" style="left:334px;top:328px;width:15px;height:15px;background:var(--dot-green)"></div>
    <div class="placeholder" role="img" aria-label="Illustration of a glowing light bulb over an open book" style="left:203px;top:292px;width:158px;height:170px;background:linear-gradient(170deg,#fbe8a6,#f6efe6 60%,#f7cfa6)"></div>
    <p class="feature" style="left:52px;top:346px;width:150px">Safe, engaging environments designed to inspire young minds</p>

    <div class="placeholder" role="img" aria-label="Illustration of a cartoon head holding pens and pencils" style="left:23px;top:462px;width:150px;height:173px;background:linear-gradient(180deg,#d9d1f4,#f6d3bb)"></div>
    <p class="feature" style="left:177px;top:522px;width:196px">Now transitioning to a Reggio Emilia-inspired approach—encouraging exploration, creativity, and child-led learning.</p>

    <div class="dot" style="left:207px;top:637px;width:15px;height:15px;background:var(--dot-green)"></div>
    <div class="dot" style="left:57px;top:675px;width:10px;height:10px;background:var(--dot-teal)"></div>
    <div class="photo" role="img" aria-label="Photo of children playing at a water table outdoors" style="left:61px;top:641px;width:182px;height:182px;background:linear-gradient(160deg,#8c7a62,#c8b9a4 50%,#6fa0a8)"></div>
    <div class="photo" role="img" aria-label="Photo of children building with colorful blocks on a rug" style="left:222px;top:625px;width:148px;height:148px;background:linear-gradient(160deg,#efe7dd,#d9b79a 55%,#8aa0c8)"></div>
    <div class="dot" style="left:237px;top:772px;width:19px;height:19px;background:var(--dot-pink)"></div>
  </section>

  <section class="panel panel--middle">
    <p class="abs discount-lead">We are also proud to offer exclusive corporate discounts for professionals in key industries:</p>
    <ul class="discount-list">
      <li><svg width="15" height="15" viewBox="0 0 16 16"><circle cx="8" cy="8" r="8" fill="var(--tick)"/><path d="M4.5 8.3l2.3 2.3 4.7-4.9" fill="none" stroke="#fff" stroke-width="2" stroke-linecap="round" stroke-linejoin="round"/></svg>Teachers.</li>
      <li><svg width="15" height="15" viewBox="0 0 16 16"><circle cx="8" cy="8" r="8" fill="var(--tick)"/><path d="M4.5 8.3l2.3 2.3 4.7-4.9" fill="none" stroke="#fff" stroke-width="2" stroke-linecap="round" stroke-linejoin="round"/></svg>Healthcare &amp; Hospital Staff.</li>
      <li><svg width="15" height="15" viewBox="0 0 16 16"><circle cx="8" cy="8" r="8" fill="var(--tick)"/><path d="M4.5 8.3l2.3 2.3 4.7-4.9" fill="none" stroke="#fff" stroke-width="2" stroke-linecap="round" stroke-linejoin="round"/></svg>Law Enforcement &amp; First Responders.</li>
      <li><svg width="15" height="15" viewBox="0 0 16 16"><circle cx="8" cy="8" r="8" fill="var(--tick)"/><path d="M4.5 8.3l2.3 2.3 4.7-4.9" fill="none" stroke="#fff" stroke-width="2" stroke-linecap="round" stroke-linejoin="round"/></svg>Military Families.</li>
      <li><svg width="15" height="15" viewBox="0 0 16 16"><circle cx="8" cy="8" r="8" fill="var(--tick)"/><path d="M4.5 8.3l2.3 2.3 4.7-4.9" fill="none" stroke="#fff" stroke-width="2" stroke-linecap="round" stroke-linejoin="round"/></svg>Employees of Partnered Businesses &amp; Apartments.</li>
    </ul>
    <p class="abs discount-close">Quality childcare should be affordable and accessible—because when families thrive, communities grow!</p>

    <div class="dot" style="left:329px;top:330px;width:10px;height:10px;background:var(--dot-teal)"></div>
    <div class="photo" role="img" aria-label="Photo of three children reaching up to stack a tall tower of cups in a classroom" style="left:28px;top:302px;width:344px;height:344px;border-width:7px;background:linear-gradient(160deg,#a9634d,#e9dfd3 45%,#e3c94b 65%,#3ab59b)"></div>
    <div class="dot" style="left:361px;top:540px;width:19px;height:19px;background:var(--dot-pink)"></div>
    <div class="dot" style="left:129px;top:652px;width:15px;height:15px;background:var(--dot-green)"></div>
    <div class="photo" role="img" aria-label="Photo of a child painting a large colorful canvas" style="left:165px;top:578px;width:238px;height:238px;border-width:7px;background:linear-gradient(150deg,#d9d24a,#7fae46 45%,#e58aa0 75%,#c7a3c9)"></div>
    <div class="dot" style="left:363px;top:808px;width:15px;height:15px;background:var(--dot-green)"></div>
  </section>

  <section class="panel panel--right">
    <h2 class="title-sticker right-title">
      <span class="title-main">Our Approach</span>
      <span class="title-sub">Learning through exploration</span>
    </h2>
    <p class="abs body-copy approach-intro">At Bright Harbor, we believe that children learn best through curiosity, hands-on discovery, and meaningful experiences. That’s why we are transitioning to a Reggio Emilia-inspired philosophy, where:</p>

    <div class="principle" style="top:230px">
      <h3><svg width="15" height="15" viewBox="0 0 16 16"><circle cx="8" cy="8" r="8" fill="var(--tick)"/><path d="M4.5 8.3l2.3 2.3 4.7-4.9" fill="none" stroke="#fff" stroke-width="2" stroke-linecap="round" stroke-linejoin="round"/></svg>Children take the lead</h3>
      <p>Learning is shaped by their interests and natural curiosity</p>
    </div>
    <div class="principle" style="top:306px">
      <h3><svg width="15" height="15" viewBox="0 0 16 16"><circle cx="8" cy="8" r="8" fill="var(--tick)"/><path d="M4.5 8.3l2.3 2.3 4.7-4.9" fill="none" stroke="#fff" stroke-width="2" stroke-linecap="round" stroke-linejoin="round"/></svg>Teachers are guides</h3>
      <p>Educators observe, support, and enrich children’s experiences</p>
    </div>
    <div class="principle" style="top:381px">
      <h3><svg width="15" height="15" viewBox="0 0 16 16"><circle cx="8" cy="8" r="8" fill="var(--tick)"/><path d="M4.5 8.3l2.3 2.3 4.7-4.9" fill="none" stroke="#fff" stroke-width="2" stroke-linecap="round" stroke-linejoin="round"/></svg>The environment is a teacher</h3>
      <p>Classrooms are designed to inspire creativity and exploration</p>
    </div>
    <div class="principle" style="top:456px">
      <h3><svg width="15" height="15" viewBox="0 0 16 16"><circle cx="8" cy="8" r="8" fill="var(--tick)"/><path d="M4.5 8.3l2.3 2.3 4.7-4.9" fill="none" stroke="#fff" stroke-width="2" stroke-linecap="round" stroke-linejoin="round"/></svg>Collaboration is key</h3>
      <p>Children, families, and educators work together in a connected learning community</p>
    </div>

    <p class="abs body-copy approach-blend">We blend this philosophy with The Playwise Framework® for Preschool and Emergent Curriculum to create a research-backed, child-centered learning experience. The Playwise Framework® builds confidence, critical thinking, and academic readiness, while Emergent Curriculum adapts lessons to children's interests—making learning engaging, meaningful, and fun.</p>
  </section>

</main>
</body>
</html>
```